We are a building company that build new homes and units we are looking for something fresh and looks good my company name is
Lark Building Co Pty Ltd

Industry/Entity Type

Building

Contact Information for Business Card

Name Marco Ellis-Dunford
Tittle: Director
Address 14 Corrin St. Pelham Vale Vic 3179
Ph: 03 9582 4063
Mobile : 0400 362 918

www.larkbuildingco.com.au
Email: sales@larkbuildingco.com.au

```html
<!DOCTYPE html>
<html lang="en">
<head>
<meta charset="utf-8">
<title>Lark Building Co – Business Card</title>
<link href="https://fonts.googleapis.com/css2?family=Kalam:wght@400&family=Michroma&family=Saira+Condensed:wght@400;600&display=swap" rel="stylesheet">
<style>
  :root {
    --charcoal: #3d3d3d;
    --charcoal-deep: #2a2a2a;
    --sky: #05a8e8;
    --white: #ffffff;
    --text-soft: #f2f2f2;
    --page: #ffffff;
  }
  * { margin: 0; padding: 0; box-sizing: border-box; }
  html, body {
    width: 1200px; height: 693px; overflow: hidden;
    background: var(--page);
  }
  .canvas { position: relative; width: 1200px; height: 693px; }

  .card { position: absolute; background: var(--charcoal); box-shadow: 0 2px 10px rgba(0,0,0,.45); overflow: hidden; }

  /* Front */
  .card-front { left: 94px; top: 53px; width: 361px; height: 586px; }
  .brand {
    position: absolute; left: 0; right: 0; top: 150px;
    display: flex; flex-direction: column; align-items: center;
  }
  .brand-square { width: 120px; height: 120px; background: var(--sky); }
  .brand-name {
    margin-top: 62px; text-align: center;
    font-family: "Michroma", sans-serif; font-size: 21px; line-height: 30px;
    letter-spacing: 2px; color: var(--white); text-transform: uppercase;
  }
  .front-rule { position: absolute; left: 0; right: 0; top: 502px; height: 6px; background: var(--white); }
  .front-band {
    position: absolute; left: 0; right: 0; top: 510px; bottom: 0;
    background: linear-gradient(180deg, #0795cf 0%, var(--sky) 18%, var(--sky) 100%);
  }
  .front-tagline {
    position: absolute; left: 38px; top: 15px;
    font-family: "Kalam", cursive; font-size: 16px; color: var(--white);
  }

  /* Back */
  .card-back { left: 498px; top: 179px; width: 613px; height: 360px; }
  .back-stripe { position: absolute; left: 0; top: 0; width: 108px; height: 100%; }
  .back-edge {
    position: absolute; left: 108px; top: 0; width: 10px; height: 100%;
    background: linear-gradient(90deg, var(--charcoal-deep), var(--charcoal));
  }
  .holder {
    position: absolute; left: 154px; top: 46px;
    font-family: "Saira Condensed", sans-serif; font-weight: 600;
    font-size: 33px; letter-spacing: 1px; color: var(--white); text-transform: uppercase;
  }
  .holder-rule {
    position: absolute; left: 154px; top: 92px; width: 445px; height: 2px;
    background: linear-gradient(90deg, #f0f0f0 0%, #bdbdbd 70%, rgba(190,190,190,0) 100%);
  }
  .contact { position: absolute; left: 158px; list-style: none;
    font-family: "Saira Condensed", sans-serif; font-size: 21px; color: var(--text-soft); }
  .contact li { display: flex; align-items: center; height: 32px; }
  .contact svg { width: 24px; height: 24px; margin-right: 13px; flex: none; }
  .contact-phones { top: 104px; }
  .contact-online { top: 183px; }
  .back-tagline {
    position: absolute; left: 152px; top: 296px;
    font-family: "Kalam", cursive; font-size: 22px; color: var(--text-soft);
  }
</style>
</head>
<body>
<main class="canvas">

  <section class="card card-front" aria-label="Card front">
    <div class="brand">
      <span class="brand-square" aria-hidden="true"></span>
      <p class="brand-name">Lark Building Co</p>
    </div>
    <div class="front-rule"></div>
    <div class="front-band">
      <p class="front-tagline">New home design and construction</p>
    </div>
  </section>

  <section class="card card-back" aria-label="Card back">
    <svg class="back-stripe" viewBox="0 0 108 360" preserveAspectRatio="none" aria-hidden="true">
      <rect width="108" height="360" fill="var(--sky)"/>
      <polygon points="0,360 108,288 108,360" fill="var(--white)"/>
    </svg>
    <div class="back-edge"></div>

    <h1 class="holder">Marco Ellis-Dunford</h1>
    <div class="holder-rule"></div>

    <ul class="contact contact-phones">
      <li>
        <svg viewBox="0 0 24 24" fill="none" stroke="#e8e8e8" stroke-width="1.4" aria-hidden="true">
          <path d="M6 3l3 4-2 2c1 3 4 6 7 7l2-2 4 3-2 3c-7 0-15-8-15-15z"/>
        </svg>
        03 9582 4063
      </li>
      <li>
        <svg viewBox="0 0 24 24" fill="none" stroke="#e8e8e8" stroke-width="1.4" aria-hidden="true">
          <rect x="6" y="2" width="12" height="20" rx="2"/>
          <rect x="8" y="5" width="8" height="12"/>
          <circle cx="12" cy="19.5" r=".8" fill="#e8e8e8"/>
        </svg>
        0400 362 918
      </li>
    </ul>

    <ul class="contact contact-online">
      <li>
        <svg viewBox="0 0 24 24" fill="none" stroke="#e8e8e8" stroke-width="1.4" aria-hidden="true">
          <rect x="4" y="5" width="16" height="11" rx="1"/>
          <path d="M2 19h20l-2-3H4z"/>
        </svg>
        www.larkbuildingco.com.au
      </li>
      <li>
        <svg viewBox="0 0 24 24" fill="none" stroke="#e8e8e8" stroke-width="1.4" aria-hidden="true">
          <rect x="2" y="6" width="20" height="13"/>
          <path d="M2 6l10 8 10-8M2 19l7-7M22 19l-7-7"/>
        </svg>
        sales@larkbuildingco.com.au
      </li>
    </ul>

    <p class="back-tagline">Quality, excellence and innovation</p>
  </section>

</main>
</body>
</html>
```